Web Design for Independent Pet Supply shop.

Larch Critter Depot is a locally owned and operated premium natural pet food store and supply company with 2 thriving retail stores in Bend, Oregon, and a home delivery service. The pet food offered is the best on the market and may be described as “holistic”. Also on offer is a vast selection of toys, training tools, treats, and other supplies, as well as dog washing services that range from "do-it yourself" to "spa." Current site: LarchCritterDepot.com. They need a new, updated and responsive site.
Likes:
Tovanels.com: Natural colors, not loud, pages in motion, simple & clean but very informative.
Dorvikmerin.com: Everything in simple big colorful blocks. The specials run across the top and in motion. This site looks very professional but simple. The information is available several different places.
Plenharvest.com: Again big blocks through out. Very Fun and inviting. Tons of information with videos and recipes and testimonials. Pleasant feel and colors as well.
Dislikes:
Furlix.com: Looks cheap, hate the colors, very busy and over whelming. Hate the old style header bar going across with options. Too many printed words instead of fun images.
Colors should be "natural" tones, warm and soothing. Deep dark blue and greys with earthy wood color.
Do Not Use: Blue violet, violet, red violet

```html
<!DOCTYPE html>
<html lang="en">
<head>
<meta charset="utf-8">
<title>Larch Critter Depot</title>
<link href="https://fonts.googleapis.com/css2?family=Anton&family=Arimo:wght@400;700&family=Open+Sans:ital,wght@0,400;0,600;1,400&display=swap" rel="stylesheet">
<style>
:root{
  --brown:#b97b36;
  --brown-dark:#9a6426;
  --gold-line:#d9b98c;
  --ivory:#f7f3ea;
  --grey-band:#f0f0f0;
  --text:#555;
  --white:#fff;
}
*{box-sizing:border-box;margin:0;padding:0}
html,body{width:735px;height:1200px;overflow:hidden}
body{position:relative;background:var(--ivory);font-family:"Open Sans",Arial,sans-serif;color:var(--text);font-size:7px}
.abs{position:absolute}
.topline{left:0;top:0;width:735px;height:2px;background:var(--gold-line)}
.brand{left:58px;top:30px;display:flex;align-items:center;gap:7px}
.brand-dot{width:24px;height:24px;border-radius:50%;background:var(--brown)}
.brand-name{font-family:"Arimo",Arial,sans-serif;font-weight:700;font-size:19px;color:var(--brown);letter-spacing:.2px}
.call{left:557px;top:24px;display:flex;gap:10px;align-items:center}
.call-ring{width:28px;height:28px;border:1.5px solid var(--brown);border-radius:50%;display:flex;align-items:center;justify-content:center}
.call small{display:block;font-family:"Arimo",sans-serif;font-size:9px;color:#444}
.call strong{display:block;font-family:"Arimo",sans-serif;font-size:11.5px;color:var(--brown);margin-top:4px}
.ribbon-end{top:86px;width:40px;height:34px;background:var(--brown-dark)}
.ribbon-l{left:14px;clip-path:polygon(0 0,100% 0,100% 100%,0 100%,30% 50%)}
.ribbon-r{left:681px;clip-path:polygon(0 0,100% 0,70% 50%,100% 100%,0 100%)}
.nav{left:50px;top:80px;width:635px;height:37px;background:var(--brown);display:flex;box-shadow:0 2px 3px rgba(0,0,0,.25)}
.nav a{flex:1 1 auto;color:var(--white);text-decoration:none;font-family:"Arimo",sans-serif;font-size:7.5px;display:flex;align-items:center;justify-content:center;border-right:1px solid rgba(0,0,0,.12)}
.nav a:last-child{border-right:0}
.hero-frame{left:59px;top:117px;width:617px;height:296px;background:#f3efe4;box-shadow:0 6px 8px rgba(0,0,0,.12)}
.hero-photo{left:65px;top:117px;width:605px;height:290px;background:linear-gradient(100deg,#a79f93 0%,#e9e3d8 30%,#d3b38a 55%,#b9ad9d 80%,#6d5a4a 100%)}
.hero-arc{left:295px;top:394px;width:140px;height:26px;border-radius:50% 50% 0 0;background:#f3efe4}
.hero-copy{left:75px;top:241px;width:195px;color:var(--white)}
.hero-copy .rule{width:128px;height:1.5px;background:var(--white);margin-bottom:6px}
.hero-copy h1{font-family:"Anton",sans-serif;font-weight:400;font-size:21px;letter-spacing:.5px;line-height:26px}
.hero-copy p{font-size:8px;line-height:14px;margin-top:5px}
.btn{display:inline-block;background:var(--brown);color:var(--white);font-size:7px;font-weight:600;padding:8px 19px;margin-top:6px;border-radius:1px}
.dots{left:345px;top:395px;display:flex;gap:5px;align-items:center}
.dots i{width:6px;height:6px;border-radius:50%;background:#444}
.dots i.on{width:10px;height:10px;border:1.5px solid var(--brown);background:#444;box-shadow:inset 0 0 0 1.5px #fff}
.qc{left:472px;top:140px;width:177px;height:248px;background:#f4f2ee}
.qc h2{height:32px;background:var(--brown);color:var(--white);font-family:"Arimo",sans-serif;font-weight:400;font-size:12.5px;letter-spacing:.8px;text-align:center;line-height:32px}
.field{position:absolute;left:12px;width:152px;background:var(--white);font-size:7px;color:#777;padding:0 0 0 21px;display:flex;align-items:center}
.field::before{content:"";position:absolute;left:8px;width:5px;height:5px;background:#999;border-radius:1px}
.field.msg{align-items:flex-start;padding-top:12px}
.field.msg::before{top:14px}
.qc .submit{position:absolute;left:12px;top:206px;width:152px;height:27px;background:var(--brown);color:var(--white);font-family:"Arimo",sans-serif;font-size:10px;text-align:center;line-height:27px;border-radius:2px}
.services-title{left:0;top:436px;width:735px;text-align:center}
.services-title span{display:inline-block;font-family:"Anton",sans-serif;font-size:21px;color:var(--brown);letter-spacing:.8px;border-top:1px solid var(--gold-line);border-bottom:1px solid var(--gold-line);padding:2px 1px 1px}
.svc{top:486px;width:190px;text-align:center}
.svc-ic{width:74px;height:74px;border-radius:50%;background:var(--brown);margin:0 auto;display:flex;align-items:center;justify-content:center}
.svc h3{font-family:"Arimo",sans-serif;font-weight:400;font-size:10px;color:#222;margin-top:8px}
.svc p{font-size:7px;line-height:12.5px;color:#444;margin-top:5px}
.svc em{display:block;font-size:7px;color:var(--brown);margin-top:6px}
.band{left:0;top:665px;width:735px;height:342px;background:var(--grey-band)}
.news{left:61px;top:700px;width:405px}
.news h2{font-family:"Arimo",sans-serif;font-weight:400;font-size:12.5px;color:#222;line-height:24px}
.news p{font-size:7px;line-height:14.2px;color:#555;margin-top:4px}
.news p+p{margin-top:14px}
.paws{left:60px;top:900px;width:305px;height:80px;background:var(--white);padding:3px;box-shadow:0 1px 3px rgba(0,0,0,.25)}
.paws div{width:100%;height:100%;background:linear-gradient(90deg,#3b3b3b 0%,#8a7a62 30%,#4a4845 50%,#9a8466 75%,#3e3d3a 100%)}
.social{left:483px;top:700px;width:190px;height:280px;background:var(--white);box-shadow:0 1px 4px rgba(0,0,0,.2);padding:18px 18px 0 20px}
.social-head{display:flex;align-items:center;gap:6px}
.social-head .ring{width:32px;height:32px;border-radius:50%;border:3px solid #d4b483}
.social-head strong{font-family:"Arimo",sans-serif;font-size:11px;color:#3b5596}
.social-head small{display:block;font-size:5px;color:#444;margin-top:5px}
.post{display:flex;gap:8px;margin-top:12px}
.post .thumb{width:37px;height:34px;flex:none}
.post b{display:block;font-weight:400;font-size:7.5px;color:#222}
.post span{display:block;font-size:5.5px;color:#555;margin-top:3px}
.post i{display:block;font-style:normal;font-size:5.5px;color:#333;margin-top:5px}
.fans-cap{font-size:4.5px;color:#333;margin-top:12px}
.fans{width:148px;height:41px;margin-top:4px;background:linear-gradient(90deg,#8d6e5a,#c9a58b,#6d5a52,#d6b6a0,#7a6156)}
.fans-foot{font-size:4px;color:#666;margin-top:5px;border-top:1px solid #ddd;padding-top:2px}
.footer{left:0;top:1007px;width:735px;height:166px;background:var(--brown)}
.foot-col{top:1027px;color:var(--white)}
.foot-col h4{font-family:"Arimo",sans-serif;font-weight:400;font-size:12.5px;padding-bottom:4px;border-bottom:1px solid rgba(255,255,255,.6);display:inline-block;padding-right:2px}
.hours{font-size:7px;line-height:13.5px;margin-top:9px;padding-left:13px;position:relative}
.hours::before{content:"";position:absolute;left:1px;top:3px;width:5px;height:5px;border:1.3px solid #fff;border-radius:50%}
.links{list-style:none;font-size:7px;line-height:11.6px;margin-top:7px}
.links li::before{content:"›";margin-right:5px}
.tweet{display:flex;gap:12px;margin-top:10px}
.tweet .dot{width:10px;height:9px;border-radius:50%;background:#fff;flex:none;margin-top:4px}
.tweet b{display:block;font-weight:400;font-size:8px}
.tweet span{display:block;font-size:5.5px;line-height:9.5px}
.tweet em{display:block;font-size:5.5px;line-height:9.5px}
.contact-row{display:flex;gap:10px;align-items:flex-start;font-size:7px;line-height:11px;margin-top:12px}
.contact-row .big{font-family:"Arimo",sans-serif;font-size:9.5px}
.bottombar{left:0;top:1173px;width:735px;height:27px;background:var(--brown-dark);color:var(--white)}
.bottombar .copy{position:absolute;left:61px;top:9px;font-size:7px}
.bottombar .icons{position:absolute;left:575px;top:4px;display:flex;gap:5px}
.bottombar .icons i{width:18px;height:18px;border:1.2px solid #fff;border-radius:50%}
.bottombar .code{position:absolute;left:700px;top:9px;font-size:7px}
</style>
</head>
<body>
<div class="abs topline"></div>

<div class="abs brand"><span class="brand-dot"></span><span class="brand-name">Larch Critter Depot</span></div>

<div class="abs call">
  <div class="call-ring"><svg width="12" height="12" viewBox="0 0 24 24"><path d="M6.6 10.8a15 15 0 0 0 6.6 6.6l2.2-2.2c.3-.3.7-.4 1-.2 1.1.4 2.3.6 3.6.6.6 0 1 .4 1 1V20c0 .6-.4 1-1 1C10.6 21 3 13.4 3 4c0-.6.4-1 1-1h3.5c.6 0 1 .4 1 1 0 1.3.2 2.5.6 3.6.1.3 0 .7-.2 1z" fill="#b97b36"/></svg></div>
  <div><small>Call Us Now!</small><strong>541-555-0142</strong></div>
</div>

<div class="abs ribbon-end ribbon-l"></div>
<div class="abs ribbon-end ribbon-r"></div>
<nav class="abs nav">
  <a>HOME</a><a>EVENTS</a><a>BLOG</a><a>ABOUT</a><a>DOG WASH</a><a>PRODUCTS</a><a>RESOURCES</a><a>LINKS</a><a>CONTACT</a>
</nav>

<div class="abs hero-frame"></div>
<div class="abs hero-photo" role="img" aria-label="Photo of a light-coated dog eating from a steel bowl on a tiled floor"></div>
<div class="abs hero-arc"></div>
<div class="abs hero-copy">
  <div class="rule"></div>
  <h1>HAPPY FALL</h1>
  <p>The Larch Critter Depot Dog Wash attendants are always here to help wash your four legged friends, and trim their nails</p>
  <span class="btn">View more</span>
</div>
<div class="abs dots"><i class="on"></i><i></i><i></i><i></i></div>

<form class="abs qc">
  <h2>QUICK CONTACT</h2>
  <div class="field" style="top:44px;height:26px">Enter your name</div>
  <div class="field" style="top:76px;height:25px">Enter your email address</div>
  <div class="field" style="top:107px;height:25px">Phone number</div>
  <div class="field msg" style="top:139px;height:55px">Enter your message</div>
  <div class="submit">SUBMIT</div>
</form>

<div class="abs services-title"><span>SERVICES WE OFFER</span></div>

<div class="abs svc" style="left:36px">
  <div class="svc-ic"><svg width="38" height="34" viewBox="0 0 38 34" fill="none" stroke="#fff" stroke-width="2"><rect x="4" y="3" width="14" height="20" rx="2"/><path d="M8 25h26l-3 6H11z"/><circle cx="11" cy="13" r="3"/></svg></div>
  <h3>Pup Brew</h3>
  <p>Now you can pour some cold brew for<br>your pup in a fun and easy way that has a<br>delicious flavor and packed full...</p>
  <em>Read more</em>
</div>
<div class="abs svc" style="left:272px">
  <div class="svc-ic"><svg width="44" height="26" viewBox="0 0 44 26" fill="none" stroke="#fff" stroke-width="2"><path d="M10 10c0-5 24-5 24 0"/><path d="M4 11h36l-5 12H9z"/></svg></div>
  <h3>Kibbleford Lawsuit</h3>
  <p>Kibbleford is being sued by , Dale Marwick of<br>Harbor Point, Oregon. He he first<br>purchased Tailsome food in December or</p>
  <em>Read more</em>
</div>
<div class="abs svc" style="left:478px">
  <div class="svc-ic"><svg width="30" height="40" viewBox="0 0 30 40" fill="none" stroke="#fff" stroke-width="2.2"><rect x="4" y="3" width="8" height="14" rx="4"/><path d="M8 17v18"/><circle cx="8" cy="36" r="2"/><circle cx="22" cy="9" r="5"/><path d="M22 14v21"/><circle cx="22" cy="36" r="2"/></svg></div>
  <h3>Driftline 5/8" Leads On Sale</h3>
  <p>Your local Driftline has ALL of their 5/8"<br>Leads ON SALE for just $10!</p>
  <em>Read more</em>
</div>

<div class="abs band"></div>
<section class="abs news">
  <h2>THE LARCH CRITTER DEPOT DOG WASH<br>NEWS AND UPDATES</h2>
  <p>The Larch Critter Depot Dog Wash attendants are always here to help wash your four-legged friends, and trim their nails...but they are also here to help educate all of us! Nail trims are such an essential routine for our pups, especially if they don't run and walk as much as they would in the wild.</p>
  <p>Below are two photo that demonstrate how important nail trims are. The 'Before' shot shows the dogs two front feet. Looking at the photo the left foot ( Dogs right foot) has not been trimmed yet. Notice the two outside toes twisting out and away from the foot. The right foot ( Dogs left foot ) has already been trimmed. Notice how "cat like" the toes are, tight and together allowing the pads full access to the ground in a healthy way. Dog toe/foot pads relay information to the dog like where the ground is, what angle the slope/stairs are, etc. When toes get twisted due to long nails, signals get mixed and dogs start trying to compensate by standing differently resulting</p>
</section>
<div class="abs paws"><div role="img" aria-label="Before and after photos of a dog's front paws with the toes circled"></div></div>

<aside class="abs social">
  <div class="social-head"><span class="ring"></span><div><strong>Social Feed</strong><small>Like &nbsp; you like this.</small></div></div>
  <div class="post"><div class="thumb" role="img" aria-label="Photo of a dog" style="background:#8c6a45"></div><div><b>Finibus Bonorum et Malorum</b><span>Lorem ipsum dolor sit amet</span><i>20 Likes &nbsp; Share</i></div></div>
  <div class="post"><div class="thumb" role="img" aria-label="Photo of an owner with a dog" style="background:#6f6a66"></div><div><b>Perspiciatis unde omnis unde</b><span>Lorem ipsum dolor sit amet</span><i>20 Likes &nbsp; Share</i></div></div>
  <div class="post"><div class="thumb" role="img" aria-label="Photo of an owner with a pet" style="background:#9a7c5c"></div><div><b>Perspiciatis unde omnis unde</b><span>Lorem ipsum dolor sit amet</span><i>20 Likes &nbsp; Share</i></div></div>
  <div class="fans-cap">You and 19 others like LCD.</div>
  <div class="fans" role="img" aria-label="Grid of follower profile photos"></div>
  <div class="fans-foot">Social page plugin</div>
</aside>

<footer class="abs footer"></footer>
<div class="abs foot-col" style="left:60px">
  <h4>OPENING HOURS</h4>
  <div class="hours">Monday – Saturday 9 a.m. – 6 p.m.<br>Sunday &nbsp;10 a.m. – 4 p.m<br>Dog Wash:9 a.m.-5:30 p.m.</div>
</div>
<div class="abs foot-col" style="left:237px">
  <h4>QUICK LINKS</h4>
  <ul class="links"><li>Home</li><li>Events</li><li>Blog</li><li>About</li><li>Dog Wash</li><li>Products</li><li>Resources</li><li>Links</li><li>Contact</li></ul>
</div>
<div class="abs foot-col" style="left:375px">
  <h4>LATEST UPDATES</h4>
  <div class="tweet"><span class="dot"></span><div><b>Finibus Bonorum et</b><span>Lorem Ipsum is simply dummy<br>text of the printing</span><em>http://larchcritterdepot.com/<br>24 Minites ago</em></div></div>
  <div class="tweet"><span class="dot"></span><div><b>Finibus Bonorum et</b><span>Lorem Ipsum is simply dummy</span><em>http://larchcritterdepot.com/<br>24 Minites ago</em></div></div>
</div>
<div class="abs foot-col" style="left:548px">
  <h4>CONTACT US</h4>
  <div class="contact-row"><svg width="8" height="11" viewBox="0 0 10 14"><path d="M5 0a5 5 0 0 1 5 5c0 4-5 9-5 9S0 9 0 5a5 5 0 0 1 5-5z" fill="#fff"/><circle cx="5" cy="5" r="1.8" fill="#b97b36"/></svg><span>418 NE Cedar Hollow Dr.<br>Larch, OR 97709</span></div>
  <div class="contact-row" style="margin-top:7px"><svg width="10" height="10" viewBox="0 0 24 24"><path d="M6.6 10.8a15 15 0 0 0 6.6 6.6l2.2-2.2c.3-.3.7-.4 1-.2 1.1.4 2.3.6 3.6.6.6 0 1 .4 1 1V20c0 .6-.4 1-1 1C10.6 21 3 13.4 3 4c0-.6.4-1 1-1h3.5c.6 0 1 .4 1 1 0 1.3.2 2.5.6 3.6.1.3 0 .7-.2 1z" fill="#fff"/></svg><span class="big">541-555-0142</span></div>
  <div class="contact-row" style="margin-top:8px"><svg width="11" height="8" viewBox="0 0 14 10"><rect width="14" height="10" fill="#fff"/><path d="M0 0l7 6 7-6" fill="none" stroke="#b97b36"/></svg><span>eastside@larchcritterdepot.com</span></div>
</div>
<div class="abs bottombar">
  <span class="copy">Copyright 2015 .LarchCritterDepot. All Rights Reserved</span>
  <div class="icons"><i></i><i></i><i></i><i></i><i></i></div>
  <span class="code">C12</span>
</div>
</body>
</html>
```